Podiatry clinic requires a modern revamp and editing of existing website.

I would like a fresh new look and updated information for my current business website. An easy to navigate site with prominent address and phone number for call to action. We are a podiatry clinic that focuses on general and sports podiatry.
I would like 4 pages; including Home page, About Us, Services & Contact.
www.brambleridgepodiatry.net

Target Market(s)

Active working professionals.

Industry/Entity Type

Medical

Coding

Coded - Design and coding required

Number of Pages Required

4 page

Font styles to use
Sans Serif

Colors
6b449b

Requirements
Must have
• A modern look with logo and active images; clean and uncluttered. Visible phone number and address for call to action.
• 4 pages - Home, About Us, Services, Contact.
• Home page - update address & service logos.
• About Us - update of personal information.
• Services - Revamp of existing page.
• Contact page to include Google map, email & phone number.
Nice to have
• Ability to add content easily; eg. a blog or adding video onto Home page.
• Link to Facebook page.

```html
<!DOCTYPE html>
<html lang="en">
<head>
<meta charset="utf-8">
<title>Bramble Ridge Podiatry</title>
<link rel="stylesheet" href="https://fonts.googleapis.com/css2?family=Raleway:wght@400;500;600&family=Open+Sans:wght@400;600&family=Roboto+Condensed:wght@400;700&display=swap">
<style>
:root{
  --brand:#6b449b;
  --nav:#4a2f94;
  --ink-purple:#3d2a8f;
  --green:#7bbf2a;
  --grey:#555;
  --white:#fff;
  --footer:#5a36a8;
}
*{box-sizing:border-box;margin:0;padding:0}
html,body{width:1200px;height:2276px;overflow:hidden}
body{font-family:"Open Sans",sans-serif;background:var(--white);color:var(--grey);position:relative}
.wrap{position:absolute;left:77px;width:1047px}

.site-header{position:absolute;top:0;left:0;width:1200px;height:175px;background:linear-gradient(#6f4fbe,#8a73cc 45%,#f4f2fb)}
.brand{position:absolute;left:80px;top:38px;display:flex;align-items:center;gap:14px}
.brand-dot{width:36px;height:36px;border-radius:50%;background:var(--white)}
.brand-name{font-family:"Raleway",sans-serif;font-weight:600;font-size:30px;line-height:1.1;color:var(--white)}
.header-contact{position:absolute;right:83px;top:44px;text-align:right;font-family:"Roboto Condensed",sans-serif;color:var(--white);font-size:21px}
.header-contact p{display:flex;align-items:center;justify-content:flex-end;gap:10px;margin-bottom:20px}
.header-contact b{font-weight:700}

.main-nav{position:absolute;top:175px;left:0;width:1200px;height:63px;background:var(--nav)}
.main-nav ul{list-style:none;display:flex;position:absolute;left:77px;top:0;height:63px}
.main-nav li{font-family:"Raleway",sans-serif;font-size:19px;color:var(--white);padding:0 36px;line-height:63px}
.main-nav li.active{background:var(--green)}

.hero-foot{position:absolute;left:0;top:238px;width:152px;height:250px;background:linear-gradient(160deg,#eee,#d8c4b8 55%,#e0483a)}
.services-intro{top:294px;text-align:center}
.section-title{font-family:"Raleway",sans-serif;font-weight:400;font-size:42px;color:#555}
.section-title span{color:var(--ink-purple)}
.services-intro p{font-size:15.5px;line-height:25px;width:760px;margin:14px auto 0;color:#555}
.sub-title{font-family:"Raleway",sans-serif;font-weight:400;font-size:32px;color:#555;margin-top:36px}
.sub-title span{color:var(--ink-purple)}

.treatments{display:grid;grid-template-columns:repeat(4,235px);column-gap:37px;row-gap:0}
.general{top:525px}
.treatment .photo{height:140px}
.treatment h3{font-family:"Raleway",sans-serif;font-weight:400;font-size:20px;line-height:31px;color:var(--ink-purple);text-align:center;margin-top:12px;height:78px}

.specialised{position:absolute;top:1021px;left:0;width:1200px;height:458px;background:linear-gradient(#5a3fae,#7a63c1 50%,#ddd6ef)}
.specialised .section-sub{position:absolute;top:48px;width:1200px;text-align:center;font-family:"Raleway",sans-serif;font-weight:400;font-size:32px;color:var(--white)}
.special-grid{position:absolute;top:112px;left:77px;display:grid;grid-template-columns:repeat(5,188px);column-gap:26px}
.special-grid .photo{height:125px}
.special-grid h3{font-family:"Raleway",sans-serif;font-weight:400;font-size:20px;line-height:31px;color:var(--white);text-align:center;margin-top:12px}
.cta{position:absolute;top:344px;left:422px;width:356px;height:50px;border-radius:25px;background:var(--nav);color:var(--white);font-family:"Raleway",sans-serif;font-size:22px;text-align:center;line-height:50px}

.partners{position:absolute;top:1479px;left:0;width:1200px;height:193px;display:flex;justify-content:space-between;align-items:center;padding:0 77px}
.badge{width:230px;height:90px;border-radius:8px;background:#e6e2ef}

.contact{position:absolute;top:1672px;left:0;width:1200px;height:550px;background:linear-gradient(180deg,#3e4a33,#5c6848 45%,#2e2f2a)}
.contact h2{position:absolute;top:46px;width:1200px;text-align:center;font-family:"Raleway",sans-serif;font-weight:400;font-size:42px;color:var(--white)}
.contact-form{position:absolute;left:77px;top:156px;width:437px}
.field{width:437px;height:48px;background:var(--white);border-radius:5px;margin-bottom:10px;padding:12px 17px;font-size:14px;color:#888}
.field.message{height:103px}
.submit{width:166px;height:50px;border-radius:25px;background:var(--brand);color:var(--white);font-family:"Raleway",sans-serif;font-weight:600;font-size:23px;text-align:center;line-height:50px;margin-top:6px}
.map{position:absolute;left:535px;top:156px;width:275px;height:275px;background:linear-gradient(135deg,#ecebe6,#e0ded6)}
.address{position:absolute;left:854px;top:150px;width:300px;color:var(--white)}
.address h4{font-family:"Raleway",sans-serif;font-weight:400;font-size:21px;margin-bottom:26px}
.address p{display:flex;gap:16px;font-size:15px;line-height:22px;margin-bottom:18px}
.address p svg{flex:none}
.social{width:46px;height:46px;border-radius:50%;background:var(--white);margin-left:0}

.site-footer{position:absolute;top:2222px;left:0;width:1200px;height:54px;background:var(--footer);color:var(--white);text-align:center;line-height:54px;font-size:15px}
</style>
</head>
<body>
<header class="site-header">
  <div class="brand"><span class="brand-dot"></span><span class="brand-name">bramble ridge<br>podiatry</span></div>
  <div class="header-contact">
    <p><svg width="18" height="24" viewBox="0 0 18 24"><path d="M9 0a9 9 0 0 0-9 9c0 7 9 15 9 15s9-8 9-15a9 9 0 0 0-9-9z" fill="#fff"/><circle cx="9" cy="9" r="3.5" fill="#7a62c8"/></svg>Suite 12 / 88 Harlow Lane Kestrel Vale 4021</p>
    <p><svg width="26" height="26" viewBox="0 0 24 24"><path d="M6.6 10.8a15 15 0 0 0 6.6 6.6l2.2-2.2a1 1 0 0 1 1-.25 11.4 11.4 0 0 0 3.6.57 1 1 0 0 1 1 1V20a1 1 0 0 1-1 1A17 17 0 0 1 3 4a1 1 0 0 1 1-1h3.5a1 1 0 0 1 1 1c0 1.25.2 2.45.57 3.6a1 1 0 0 1-.25 1z" fill="#fff"/></svg>CALL US NOW : <b>1300 555 042</b></p>
  </div>
</header>

<nav class="main-nav">
  <ul><li class="active">HOME</li><li>ABOUT</li><li>SERVICES</li><li>CONTACT</li></ul>
</nav>

<div class="hero-foot" role="img" aria-label="Photo of hands holding a sore heel"></div>

<section class="wrap services-intro">
  <h1 class="section-title">SERVICES <span>WE PROVIDE</span></h1>
  <p>Podiatrists are trained to diagnose and treat all medical conditions that affect the feet and lower limb. At Bramble Ridge Podiatry we provide treatment for general &amp; Sports Podiatry conditions and various specialised treatments:</p>
  <h2 class="sub-title">General <span>Treatments</span></h2>
</section>

<section class="wrap treatments general">
  <div class="treatment"><div class="photo" role="img" aria-label="Photo of toenail care" style="background:linear-gradient(135deg,#f1ede8,#e6c4b0)"></div><h3>Nails</h3></div>
  <div class="treatment"><div class="photo" role="img" aria-label="Photo of corn treatment" style="background:linear-gradient(135deg,#2a2624,#c7a48e)"></div><h3>Corns</h3></div>
  <div class="treatment"><div class="photo" role="img" aria-label="Photo of callus removal" style="background:linear-gradient(135deg,#e9e4df,#c89a7d)"></div><h3>Callus</h3></div>
  <div class="treatment"><div class="photo" role="img" aria-label="Photo of a wart examination" style="background:linear-gradient(135deg,#dfe9f1,#e8cdbb)"></div><h3>Warts</h3></div>
  <div class="treatment"><div class="photo" role="img" aria-label="Photo of skin treatment on a foot" style="background:linear-gradient(135deg,#7fb2cc,#e6c3b2)"></div><h3>Skin Disorders</h3></div>
  <div class="treatment"><div class="photo" role="img" aria-label="Photo of a painful heel" style="background:linear-gradient(135deg,#f3f1f0,#e3b5a2)"></div><h3>Heel pain / Heel Spurs<br>/ Arch pain</h3></div>
  <div class="treatment"><div class="photo" role="img" aria-label="Photo of a painful ankle" style="background:linear-gradient(135deg,#fafafa,#e8d6d0);border:1px solid #ccc"></div><h3>Ankle pain / Shin<br>splints / Knee pain</h3></div>
  <div class="treatment"><div class="photo" role="img" aria-label="Photo of feet beside running shoes" style="background:linear-gradient(135deg,#7a5138,#3c7bb0 60%,#8a5a3c)"></div><h3>Bunions / Hammertoes<br>/ Toe deformities</h3></div>
</section>

<section class="specialised">
  <h2 class="section-sub">Specialised Treatments</h2>
  <div class="special-grid">
    <div><div class="photo" role="img" aria-label="Photo of a foot massage" style="background:linear-gradient(135deg,#8fa46a,#c88e6b)"></div><h3>Diabetic<br>Management</h3></div>
    <div><div class="photo" role="img" aria-label="Photo of nail surgery" style="background:linear-gradient(135deg,#f2f2f2,#e2bba6)"></div><h3>Nail Surgery</h3></div>
    <div><div class="photo" role="img" aria-label="Photo of a foot assessment" style="background:linear-gradient(135deg,#f5efe8,#e0b79c)"></div><h3>Biomechanical<br>Assessment</h3></div>
    <div><div class="photo" role="img" aria-label="Photo of a runner on a road" style="background:linear-gradient(180deg,#8aa0b4,#4c4f52)"></div><h3>Gait Analysis</h3></div>
    <div><div class="photo" role="img" aria-label="Photo of hands supporting a foot" style="background:linear-gradient(135deg,#f7f3f0,#e7b8a0)"></div><h3>Orthotic Therapy</h3></div>
  </div>
  <div class="cta">Call now for an appointment</div>
</section>

<section class="partners">
  <div class="badge" role="img" aria-label="Partner badge"></div>
  <div class="badge" role="img" aria-label="Partner badge"></div>
  <div class="badge" role="img" aria-label="Partner badge"></div>
  <div class="badge" role="img" aria-label="Partner badge"></div>
</section>

<section class="contact" role="region" aria-label="Contact section over a photo of a runner on a country path">
  <h2>CONTACT US</h2>
  <div class="contact-form">
    <div class="field">Name</div>
    <div class="field">E-Mail</div>
    <div class="field">Phone</div>
    <div class="field message">Message</div>
    <div class="submit">SUBMIT</div>
  </div>
  <div class="map" role="img" aria-label="Street map showing the clinic location"></div>
  <div class="address">
    <h4>CONTACT ADDRESS</h4>
    <p><svg width="20" height="24" viewBox="0 0 18 24"><path d="M9 1a8 8 0 0 0-8 8c0 6 8 14 8 14s8-8 8-14a8 8 0 0 0-8-8z" fill="none" stroke="#fff" stroke-width="1.5"/><circle cx="9" cy="9" r="3" fill="none" stroke="#fff" stroke-width="1.5"/></svg>Suite 12 / 88 Harlow Lane<br>Kestrel Vale 4021.</p>
    <p><svg width="20" height="20" viewBox="0 0 24 24"><path d="M6.6 10.8a15 15 0 0 0 6.6 6.6l2.2-2.2a1 1 0 0 1 1-.25 11.4 11.4 0 0 0 3.6.57 1 1 0 0 1 1 1V20a1 1 0 0 1-1 1A17 17 0 0 1 3 4a1 1 0 0 1 1-1h3.5a1 1 0 0 1 1 1c0 1.25.2 2.45.57 3.6a1 1 0 0 1-.25 1z" fill="none" stroke="#fff" stroke-width="1.6"/></svg><b>1300 555 042</b></p>
    <p><svg width="20" height="16" viewBox="0 0 20 16"><rect x="1" y="1" width="18" height="14" fill="none" stroke="#fff" stroke-width="1.5"/><path d="M1 1l9 8 9-8" fill="none" stroke="#fff" stroke-width="1.5"/></svg>info@brambleridgepodiatry.net</p>
    <div class="social" role="img" aria-label="Social page link"></div>
  </div>
</section>

<footer class="site-footer">© Bramble Ridge Podiatry- 2016. All Rights Reserved.</footer>
</body>
</html>
```